Redesign of norbacute.com website (3 page types)

We need a fresh rebrush of www.norbacute.com, a portal for french regions, departements and cities. It shall look modern as the current design is over 10 years old.

We like the blueish colors and the french touch (blue, white, red).

There are 3 page types that we currently need:
- Homepage (http://www.norbacute.com/)
- Region overview (e.g. http://www.norbacute.com/provence-alpes-cote-d-azur)
- City overview (e.g. http://www.norbacute.com/provence-alpes-cote-d-azur/bouches-du-rhone/marseille)

See "Must have" for a more detailed briefing. All required elements exist and need a rebrush/redesign

Requirements
Must have
• General:

- 3 column layout
+ Header
+ Left sidebar
+ Content area
+ Right sidebar (250px inner width for ads)
+ Footer
- 3 classes of headlines
- Simple sidebar widgets (headline & content / without headline)

Header:
- Logo
- 2 or 3 links
- Search box
- Breadcrumb navigation

Footer:
- Nothing special, really

Homepage:
- Nice looking map with visible region borders to create a mouseover effect (as seen on current version). Meaning we need the plain map and a version with each region highlighted
- Text areas
- Content boxes (like the current gray ones)

Region overview
- Headline
- Info box (Informations)
- Mini map
- Crest / emblem
- Text area with headline for a long descriptive text with a "read more" / "show less" button/link to pop out the whole text via javascript
- List of the 24 biggest cities in the region

City overview
- Headline
- Info box (Informations, same look as for regions)
- Mini map
- List of the 24 cities nearby
- List of available photos
- Example sidebar widgets (right sidebar):
+ Upload a photo of this city
+ Weather conditions
+ Link list
Nice to have
• - A new favicon
- Chatterly og:image
Should not have
• - Flash
- Animations

```html
<!DOCTYPE html>
<html lang="fr">
<head>
<meta charset="utf-8">
<title>norbacute — Les villes de France</title>
<link rel="stylesheet" href="https://fonts.googleapis.com/css2?family=Source+Sans+3:ital,wght@0,400;0,600;0,700;1,400;1,600&display=swap">
<style>
:root{
  --blue:#35658f;
  --blue-dark:#2b5678;
  --blue-soft:#c9ddf0;
  --red:#8b1c17;
  --ink:#333;
  --muted:#8f8f8f;
  --text:#555;
  --white:#fff;
}
*{margin:0;padding:0;box-sizing:border-box}
html,body{width:1200px;height:2782px;overflow:hidden}
body{font-family:"Source Sans 3",sans-serif;color:var(--text);background:linear-gradient(160deg,#f4f5f6,#e7eaec 50%,#f1f2f3);position:relative}
a{text-decoration:none;color:inherit}
ul{list-style:none}
.abs{position:absolute}

/* header */
.topbar{left:0;top:0;width:1200px;height:78px;background:var(--white)}
.topbar-red{left:890px;top:0;width:310px;height:78px;background:var(--red)}
.logo{left:87px;top:30px;height:60px;display:flex;align-items:center;gap:10px;font-size:32px;font-weight:700;color:var(--red);white-space:nowrap}
.logo .mark{width:22px;height:22px;background:var(--blue)}
.nav{left:418px;top:20px;display:flex;gap:14px}
.nav a{font-size:16px;text-transform:uppercase;color:var(--ink);padding:6px 8px}
.nav a.active{background:var(--blue);color:var(--white)}
.search{left:916px;top:19px;width:197px;height:37px;background:var(--white);display:flex;align-items:center;justify-content:space-between;padding:0 12px;font-style:italic;font-size:15px;color:#999}
.hero{left:0;top:78px;width:1200px;height:300px;background:linear-gradient(180deg,#9aa3ad 0%,#b9a58a 55%,#a87a4c 100%)}
.hero-title{left:0;top:140px;width:1200px;text-align:center;font-size:60px;font-weight:700;color:var(--white);text-shadow:0 2px 6px rgba(0,0,0,.45)}
.hero-sub{left:0;top:224px;width:1200px;text-align:center;font-size:19px;color:var(--white);text-shadow:0 1px 3px rgba(0,0,0,.5)}
.dots{left:804px;top:339px;display:flex;gap:12px}
.dots i{width:11px;height:11px;border-radius:50%;background:rgba(255,255,255,.6)}
.dots i:first-child{background:var(--white)}

/* widgets */
.widget{background:var(--blue-soft)}
.widget h3{background:var(--blue);color:var(--white);font-size:18px;font-weight:700;padding:0 20px;height:46px;line-height:46px;white-space:nowrap}
.widget ul{padding:10px 20px 16px}
.widget li{font-size:15.5px;line-height:25.2px;color:var(--text)}
.widget p{font-size:15.5px;padding:10px 20px 12px}
.side-left{left:67px;top:319px;width:239px}
.side-right{left:894px;top:319px;width:238px}
.side-right .widget{margin-bottom:22px}
.photo-slot{margin:20px 24px 18px;width:107px;height:60px;background:#928a74}

/* center */
.map{left:427px;top:334px;width:426px;height:399px;background:radial-gradient(circle at 50% 45%,#3f6e98,#2e5b83 70%,rgba(46,91,131,0) 71%)}
.map-label{left:738px;top:578px;width:110px;background:var(--blue-dark);color:var(--white);font-size:11px;line-height:14px;padding:5px 8px;text-align:center}
.intro{left:361px;top:760px;width:480px;text-align:center;font-size:15px;line-height:33.4px;color:var(--text)}
.intro p{margin-bottom:36px}

h2.section{font-size:28px;font-weight:700;color:var(--blue)}
.cities-h{left:87px;top:1188px}
.card{top:1248px;width:241px}
.card .img{height:114px}
.card h4{margin-top:84px;font-size:17px;font-weight:700;color:var(--ink)}
.card p{margin-top:8px;height:170px;overflow:hidden;font-size:15px;line-height:24.3px;color:#9a9a9a}
.card p b{color:#777;font-weight:600}
.more{display:block;text-align:right;font-style:italic;font-size:15.5px;color:var(--blue)}
.card .more{margin-top:24px}

.news-h{left:87px;top:1750px}
.news{width:510px;height:152px}
.news .thumb{position:absolute;left:0;top:0;width:154px;height:152px;background:var(--blue-soft)}
.news .body{position:absolute;left:175px;top:0;width:335px;height:152px}
.news h4{font-size:17.5px;line-height:23px;font-weight:700;color:var(--ink)}
.news p{margin-top:8px;font-size:14.6px;line-height:21px;height:63px;overflow:hidden;color:var(--muted)}
.news .more{position:absolute;right:0;top:126px}

/* footer */
.footer{left:0;top:2408px;width:1200px;height:374px;background:linear-gradient(180deg,#3d6e98,#2e5c84)}
.foot-text{color:var(--white)}
.f-logo{left:87px;top:2436px;display:flex;align-items:center;gap:8px;font-size:28px;font-weight:700}
.f-logo .mark{width:18px;height:18px;background:var(--white)}
.f-copy{left:87px;top:2505px;font-size:14.5px}
.f-links{left:87px;top:2557px;font-size:15px;line-height:26px}
.f-col h5{font-size:16px;font-weight:600;text-transform:uppercase;letter-spacing:.3px;margin-bottom:16px}
.f-cities li{font-size:15.5px;font-weight:600;line-height:36px}
.f-news h6{font-size:15.5px;font-weight:600;line-height:21px}
.f-news .meta{margin-top:18px;font-size:13px;font-style:italic}
.f-news p{margin-top:18px;font-size:15px;line-height:21px}
.f-news .more{text-align:left;color:var(--white);margin-top:12px;font-weight:600}
.f-photos{display:grid;grid-template-columns:repeat(3,67px);gap:22px 20px}
.f-photos span{height:67px}
</style>
</head>
<body>

<header>
  <div class="abs topbar"></div>
  <div class="abs topbar-red"></div>
  <div class="abs hero" role="img" aria-label="Photo panoramique de Paris avec la tour Eiffel au coucher du soleil"></div>
  <a class="abs logo" href="http://www.norbacute.com/"><span class="mark"></span>norbacute</a>
  <nav class="abs nav">
    <a class="active" href="#">Home</a><a href="#">Archives</a><a href="#">About</a><a href="#">Contact</a>
  </nav>
  <div class="abs search">Recherche
    <svg width="12" height="12" viewBox="0 0 12 12"><circle cx="5" cy="5" r="3.5" fill="none" stroke="#999" stroke-width="1.4"/><line x1="7.6" y1="7.6" x2="11" y2="11" stroke="#999" stroke-width="1.4"/></svg>
  </div>
  <h1 class="abs hero-title">Les villes de France</h1>
  <p class="abs hero-sub">Trouvez ici les régions, départements et villes français.</p>
  <div class="abs dots"><i></i><i></i><i></i><i></i></div>
</header>

<aside class="abs side-left widget">
  <h3>Les régions</h3>
  <ul>
    <li>Alsace</li><li>Aquitaine</li><li>Auvergne</li><li>Basse-Normandie</li><li>Bourgogne</li><li>Bretagne</li><li>Centre</li><li>Champagne-Ardenne</li><li>Corse</li><li>Franche-Comté</li><li>Haute-Normandie</li><li>Île-de-France</li><li>Languedoc-Roussillon</li><li>Limousin</li><li>Lorraine</li><li>Midi-Pyrénées</li><li>Nord-Pas-de-Calais</li><li>Pays de la Loire</li><li>Picardie</li><li>Poitou-Charentes</li><li>Provence-Alpes-Côte d'Azur</li><li>Rhône-Alpes</li>
  </ul>
</aside>

<aside class="abs side-right">
  <div class="widget"><h3>La France</h3><p>Statistique</p></div>
  <div class="widget"><h3>Les plus grandes villes</h3>
    <ul><li>Paris</li><li>Marseille</li><li>Lyon</li><li>Toulouse</li><li>Nice</li><li>Nantes</li><li>Strasbourg</li><li>Montpellier</li><li>Bordeaux</li><li>Lille</li><li>Rennes</li><li>Le Havre</li><li>Reims</li><li>Saint-Étienne</li><li>Toulon</li><li>Grenoble</li><li>Angers</li><li>Dijon</li><li>Brest</li><li>Le Mans</li></ul>
  </div>
  <div class="widget"><h3>Photo par hasard</h3><div class="photo-slot" role="img" aria-label="Photo choisie au hasard"></div></div>
  <div class="widget"><h3>Partenaires</h3><ul><li>La Suisse</li><li>Skiferien Alpes</li></ul></div>
</aside>

<main>
  <div class="abs map" role="img" aria-label="Carte des régions de France, région Provence-Alpes-Côte d'Azur mise en évidence en rouge"></div>
  <div class="abs map-label">Région Provence-Alpes-Côte d'Azur</div>
  <div class="abs intro">
    <p>Vous vous trouvez sur un site web dédié à vous donner toutes les informations dont vous avez besoin: Nous vous mettons à disposition une liste complète indiquant toutes les villes et tous les villages de France avec leurs codes postaux et des informations touristiques. Vous pouvez aussi télécharger les plus jolies photos de votre ville.</p>
    <p>En plus, vous trouvez ici des annonces immobilières qui vous aident à trouver la maison de vos rêves, des locaux appropriés pour votre nouveau bureau ou un petit appartement au centre-ville.</p>
    <p>Plusieurs informations supplémentaires, comme le service de météo, la possibilité d'inscrire votre propre siteweb lié à votre ville et les actualités locaux, rendent complet le total de notre offerte gratuite.</p>
  </div>

  <h2 class="abs section cities-h">Les plus belles villes du mois</h2>
  <article class="abs card" style="left:87px">
    <div class="img" role="img" aria-label="Strasbourg de nuit au bord de l'eau" style="background:linear-gradient(180deg,#1d3558,#24314a 60%,#6a5a3a)"></div>
    <h4>Strasbourg</h4>
    <p>La « capitale européenne » <b>Strasbourg</b> est aussi la capitale historique de l'Alsace à l'est de la France. Strasbourg compte 272 500 habitants et est aussi le chef-lieu du département Bas-Rhin. Au fil du développement de l'union européenne</p>
    <a class="more" href="#">Continue reading...</a>
  </article>
  <article class="abs card" style="left:349px">
    <div class="img" role="img" aria-label="Vieux-Port de Marseille et fort" style="background:linear-gradient(180deg,#8fb2cf,#b29a74 55%,#4d7a9a)"></div>
    <h4>Marseille</h4>
    <p><b>Marseille</b> n'est pas seulement la ville la plus âgée de la France - à cause de son important port commercial, elle est aussi appelée « la porte au monde ». Fondée en 600 avant J.- C. par des marins Grecs de Phocée, Marseille est le premier port de la France.</p>
    <a class="more" href="#">Continue reading...</a>
  </article>
  <article class="abs card" style="left:610px">
    <div class="img" role="img" aria-label="Village de Bormes-les-Mimosas sur la colline" style="background:linear-gradient(180deg,#a9bccb,#7d8a62 50%,#c9b49a)"></div>
    <h4>Bormes-Les-Mimosas</h4>
    <p><b>Bormes-Les-Mimosas</b> est un vieux village provençal situé sur la cote méditerranéenne au pied du massif boisé des Maures dans le département du Var. L'existence du village remonte au moins au 12ème siècle et des découvertes archéologiques permettent de dater</p>
    <a class="more" href="#">Continue reading...</a>
  </article>

  <h2 class="abs section news-h">Actualités locales</h2>
  <article class="abs news" style="left:87px;top:1814px"><div class="thumb"></div><div class="body">
    <h4>Karim Tavassoli conteste l'exclusion de son allié en Iran</h4>
    <p>par Leila Sarhadi DUBAI (Dispatch) - Le président iranien, Karim Tavassoli, a annoncé mercredi son intention de contester</p>
    <a class="more" href="#">Savoir plus...</a></div></article>
  <article class="abs news" style="left:610px;top:1814px"><div class="thumb"></div><div class="body">
    <h4>Le sommet sur l'évasion fiscale s'ouvre, pas de décision concrète attendue</h4>
    <p>Les dirigeants européens étaient réunis mercredi pour un sommet largement consacré à la lutte contre l'évasion fiscale, qui ne devrait pourtant</p>
    <a class="more" href="#">Savoir plus...</a></div></article>
  <article class="abs news" style="left:87px;top:1987px"><div class="thumb"></div><div class="body">
    <h4>Benali bientôt de retour en Algérie ?</h4>
    <p>Samir Haddad, le ministre des Affaires étrangères, a affirmé au micro de Radio Onde que l'état de santé du président algérien est "bon".</p>
    <a class="more" href="#">Savoir plus...</a></div></article>
  <article class="abs news" style="left:610px;top:1987px"><div class="thumb"></div><div class="body">
    <h4>Russie: une Velvet Choir en grève de la faim pour protester contre le tribunal</h4>
    <p>Une jeune femme du groupe contestataire russe Velvet Choir emprisonnée a annoncé mercredi entamer une grève de la faim après avoir été</p>
    <a class="more" href="#">Savoir plus...</a></div></article>
  <article class="abs news" style="left:87px;top:2161px"><div class="thumb"></div><div class="body">
    <h4>Nécessaire lutte contre l'évasion fiscale</h4>
    <p>Editorial du "Le Quotidien". Pourquoi faudrait-il prendre la mobilisation du Conseil européen contre les paradis fiscaux plus au sérieux</p>
    <a class="more" href="#">Savoir plus...</a></div></article>
  <article class="abs news" style="left:610px;top:2161px"><div class="thumb"></div><div class="body">
    <h4>La Suède ébranlée par trois nuits d'émeutes à Stockholm</h4>
    <p>par Erik Lindqvist et Nils Berg STOCKHOLM (Dispatch) - Des centaines de jeunes ont incendié des véhicules dans des banlieues de</p>
    <a class="more" href="#">Savoir plus...</a></div></article>
</main>

<footer class="foot-text">
  <div class="abs footer"></div>
  <div class="abs f-logo"><span class="mark"></span>norbacute</div>
  <p class="abs f-copy">© 2004-2013 norbacute.com</p>
  <ul class="abs f-links"><li>Home</li><li>Archives</li><li>About</li><li>Contact</li></ul>
  <div class="abs f-col f-cities" style="left:351px;top:2464px">
    <h5>Les plus belles villes</h5>
    <ul><li>Strasbourg</li><li>Marseille</li><li>Bormes-Les-Mimosas</li><li>Paris</li><li>Lyon</li></ul>
  </div>
  <div class="abs f-col f-news" style="left:612px;top:2464px;width:240px">
    <h5>Latest news</h5>
    <h6>Karim Tavassoli conteste l'exclusion de son allié en Iran</h6>
    <div class="meta">May 22, 2013 • 1 Comment</div>
    <p>par Leila Sarhadi DUBAI (Dispatch) - Le président iranien, Karim Tavassoli, a</p>
    <a class="more" href="#">Savoir plus...</a>
  </div>
  <div class="abs f-col" style="left:872px;top:2464px">
    <h5>Photos</h5>
    <div class="f-photos">
      <span role="img" aria-label="Photo de façade" style="background:linear-gradient(#6d8fb0,#8a8276)"></span>
      <span role="img" aria-label="Photo de fleur" style="background:linear-gradient(#c95a4e,#d9a14a)"></span>
      <span role="img" aria-label="Photo de cabines de plage" style="background:linear-gradient(#4d8bc4,#c7873f)"></span>
      <span role="img" aria-label="Photo de pierre" style="background:linear-gradient(#9a7c5e,#5a4632)"></span>
      <span role="img" aria-label="Photo de port" style="background:linear-gradient(#7fa6c9,#3f5f7a)"></span>
      <span role="img" aria-label="Photo de volets en bois" style="background:linear-gradient(#4a3a22,#b08c3c)"></span>
    </div>
  </div>
</footer>

</body>
</html>
```